Elegant One-Page Flyer That Catches People's Eye

For a series of workshops and zoom calls I am marketing with a colleague of mine, we would like to have an elegant, catchy one-page flyer that entices people to contact us. I am envisioning a one-page flyer (a card that is somewhat larger than a postcard) with great text, layout and images which magnetically draws people to us and is positive and inspiring. Also, if at all possible, a QR code linking it to our websites. Good colours would be shades of blue and green. I am uploading: the Text, our pictures, logos and contact information.

```html
<!DOCTYPE html>
<html lang="en">
<head>
<meta charset="utf-8">
<title>Rising Above Hidden Career Deal Breakers – Flyer</title>
<link rel="stylesheet" href="https://fonts.googleapis.com/css2?family=Poppins:wght@400;500;600;700&family=Oswald:wght@500&display=swap">
<style>
  :root{
    --bg:#b4c7cd;
    --paper:#e6e6e6;
    --green:#8aa65a;
    --maroon:#7a0f12;
    --ink:#2f2f2f;
    --text:#333;
    --dark:#1b2220;
  }
  *{margin:0;padding:0;box-sizing:border-box}
  html,body{width:927px;height:1200px;overflow:hidden}
  body{background:var(--bg);font-family:'Poppins',sans-serif;color:var(--text);position:relative}

  .flyer{position:absolute;left:33px;top:365px;width:860px;height:469px;background:var(--paper);overflow:hidden;box-shadow:0 6px 14px rgba(0,0,0,.25)}

  .hero-photo{position:absolute;right:0;top:0;width:430px;height:100%;
    background:
      linear-gradient(90deg,var(--paper) 0%,rgba(230,230,230,.6) 22%,rgba(230,230,230,0) 45%),
      linear-gradient(180deg,#c9d2d6 0%,#a9b6bb 30%,#7e8d8e 55%,#3d4a44 80%,#1f2a25 100%)}

  .kicker{position:absolute;left:37px;top:29px;font-weight:700;font-size:16px;line-height:19px;color:var(--maroon);white-space:nowrap}
  .kicker-sub{position:absolute;left:38px;top:48px;font-size:11px;line-height:14px;color:var(--text);white-space:nowrap}
  .title{position:absolute;left:37px;top:68px;font-weight:700;font-size:33px;line-height:41px;white-space:nowrap}
  .title .accent{color:var(--green);display:block}
  .title .main{color:var(--ink);display:block}

  .format-band{position:absolute;left:34px;top:168px;width:437px;height:47px;display:flex;border-radius:24px;overflow:hidden}
  .format-band .workshops{width:205px;flex:none;background:var(--green);color:#fff;font-family:'Oswald',sans-serif;font-weight:500;font-size:22px;line-height:47px;padding-left:10px;white-space:nowrap;position:relative}
  .format-band .plus{position:absolute;right:-6px;top:0;line-height:45px;font-family:'Poppins',sans-serif;font-weight:700;font-size:22px;color:#fff;z-index:2}
  .format-band .sessions{flex:1;background:var(--maroon);color:#fff;font-weight:600;font-size:10.6px;line-height:13.5px;display:flex;align-items:center;padding-left:20px;white-space:nowrap}

  .learn{position:absolute;left:41px;top:226px;z-index:2;font-weight:700;font-size:11.4px;line-height:14.5px;color:var(--maroon);background:var(--paper);padding:0 6px 4px 0;white-space:nowrap}
  .topics{position:absolute;left:41px;top:247px;width:432px;height:77px;border:1px dashed #a7b98a;border-radius:4px;padding:27px 0 0 12px;display:grid;grid-template-columns:164px 1fr;row-gap:9px;align-content:start}
  .topics-dot{position:absolute;left:306px;top:244px;z-index:3;width:6px;height:6px;border-radius:50%;background:var(--green)}
  .topics li{list-style:none;font-size:8.6px;line-height:10.5px;display:flex;gap:5px;color:var(--text)}
  .topics li svg{flex:none;margin-top:2px}

  .brand{position:absolute;white-space:nowrap;font-weight:400}
  .brand-primary{left:37px;top:355px;font-size:22px;line-height:30px;color:var(--green);display:flex;align-items:center;gap:8px}
  .brand-primary .dot{width:28px;height:28px;border:1.5px solid var(--green);border-radius:50%}
  .brand-secondary{left:46px;top:416px;font-size:12px;line-height:16px;color:var(--maroon);letter-spacing:.4px}

  .contact{position:absolute;left:231px;top:341px;width:300px;height:110px}
  .contact > *{position:absolute;left:0;white-space:nowrap}
  .contact .lead{top:0;font-weight:600;font-size:10px;line-height:13px;color:var(--dark)}
  .contact .person{font-weight:700;font-size:8.2px;line-height:11px}
  .contact .person.green{top:34px;color:var(--green)}
  .contact .person.maroon{top:72px;color:var(--maroon)}
  .contact .row{display:flex;align-items:center;font-size:9.2px;line-height:12px;font-weight:500;color:var(--dark)}
  .contact .row.first{top:47px}
  .contact .row.second{top:85px}
  .contact .row span{display:flex;align-items:center;gap:5px}
  .contact .row .phone{width:102px}

  .facilitators-tab{position:absolute;left:519px;top:205px;width:150px;height:20px;background:var(--dark);color:#fff;font-size:10px;font-weight:500;letter-spacing:4.2px;display:flex;align-items:center;padding-left:12px;border-radius:6px 0 0 6px;white-space:nowrap}
  .facilitator{position:absolute;left:512px;width:318px;height:96px;border-radius:48px;background:rgba(214,214,214,.92);border:2px solid rgba(255,255,255,.75);box-shadow:0 2px 6px rgba(0,0,0,.25)}
  .facilitator.first{top:238px}
  .facilitator.second{top:342px}
  .portrait{position:absolute;left:2px;top:1px;width:90px;height:90px;border-radius:50%;background:radial-gradient(circle at 50% 40%,#f4f4f4,#d0d0d0);border:2px solid #fff}
  .facilitator .name{position:absolute;left:102px;top:12px;font-weight:700;font-size:12.6px;line-height:16px;color:var(--maroon);white-space:nowrap}
  .facilitator .bio{position:absolute;left:102px;top:32px;width:190px;font-size:8px;line-height:10.4px;color:var(--dark)}
  .facilitator.second .name{top:14px}
  .facilitator.second .bio{top:34px;width:168px}
</style>
</head>
<body>
<main class="flyer">
  <div class="hero-photo" role="img" aria-label="Photo of a hiker with a backpack standing on a rocky summit facing snowy alpine peaks"></div>

  <h2 class="kicker">IS YOUR CAREER GOING THE WAY YOU WANT?</h2>
  <p class="kicker-sub">If not, do you feel stuck? Blocked? Frustrated? Don’t know what to do about this?</p>
  <h1 class="title"><span class="accent">Rising Above Hidden</span><span class="main">Career Deal Breakers</span></h1>

  <div class="format-band">
    <div class="workshops">4 MINI-WORKSHOPS<span class="plus">+</span></div>
    <div class="sessions">2 short Online Group Coaching<br>Sessions between Workshops</div>
  </div>

  <p class="learn">Learn to overcome and rise above<br>the 4 top hidden career deal breakers fast</p>
  <span class="topics-dot"></span>
  <ul class="topics">
    <li><svg width="7" height="7" viewBox="0 0 10 10"><circle cx="5" cy="5" r="4.2" fill="none" stroke="#8aa65a"/><path d="M3 5.2l1.5 1.4L7 3.8" fill="none" stroke="#8aa65a"/></svg>Microaggressions</li>
    <li><svg width="7" height="7" viewBox="0 0 10 10"><circle cx="5" cy="5" r="4.2" fill="none" stroke="#8aa65a"/><path d="M3 5.2l1.5 1.4L7 3.8" fill="none" stroke="#8aa65a"/></svg>Toxic black box team dynamics</li>
    <li><svg width="7" height="7" viewBox="0 0 10 10"><circle cx="5" cy="5" r="4.2" fill="none" stroke="#8aa65a"/><path d="M3 5.2l1.5 1.4L7 3.8" fill="none" stroke="#8aa65a"/></svg>Workplace snakes and other<br>dysfunctional types</li>
    <li><svg width="7" height="7" viewBox="0 0 10 10"><circle cx="5" cy="5" r="4.2" fill="none" stroke="#8aa65a"/><path d="M3 5.2l1.5 1.4L7 3.8" fill="none" stroke="#8aa65a"/></svg>Disempowering Subconscious Algorithms</li>
  </ul>

  <div class="brand brand-primary"><span class="dot"></span>TrailMind</div>
  <div class="brand brand-secondary">Vettori Coaching Zürich</div>

  <div class="contact">
    <p class="lead">For dates, venue and further information<br>Contact Clara or Maren at</p>
    <p class="person green">DR. MAREN HOLLOWAY</p>
    <div class="row first">
      <span class="phone"><svg width="8" height="8" viewBox="0 0 10 10"><path d="M2 1l2 2-1 1.2c.6 1.2 1.6 2.2 2.8 2.8L7 6l2 2-1.3 1.3C4.5 9 1 5.5.7 2.3z" fill="#8aa65a"/></svg>076 000 1234</span>
      <span><svg width="9" height="7" viewBox="0 0 10 8"><rect width="10" height="8" fill="#8aa65a"/><path d="M0 0l5 4.5L10 0" fill="none" stroke="#fff"/></svg>maren@trailmind.ch</span>
    </div>
    <p class="person maroon">DR. CLARA VETTORI</p>
    <div class="row second">
      <span class="phone"><svg width="8" height="8" viewBox="0 0 10 10"><path d="M2 1l2 2-1 1.2c.6 1.2 1.6 2.2 2.8 2.8L7 6l2 2-1.3 1.3C4.5 9 1 5.5.7 2.3z" fill="#7a0f12"/></svg>079 000 56 78</span>
      <span><svg width="9" height="7" viewBox="0 0 10 8"><rect width="10" height="8" fill="#7a0f12"/><path d="M0 0l5 4.5L10 0" fill="none" stroke="#fff"/></svg>clara@vettoricoaching.ch</span>
    </div>
  </div>

  <div class="facilitators-tab">FACILITATORS</div>

  <section class="facilitator first">
    <div class="portrait" role="img" aria-label="Portrait photo of Dr. Maren Holloway"></div>
    <h3 class="name">Dr. Maren Holloway</h3>
    <p class="bio">PhD, CPC, is an American &amp; Swiss-Trained Work &amp; Organizational Psychologist, ICF-Certified Coach, Board Certified Hypnotherapist, Certified Naturopath (TEN) &amp; Certified Ayurvedic Practitioner.</p>
  </section>

  <section class="facilitator second">
    <div class="portrait" role="img" aria-label="Portrait photo of Dr. Clara Vettori"></div>
    <h3 class="name">Dr. Clara Vettori</h3>
    <p class="bio">Ph.D., PCC is a coach and somatic experience practitioner, a team coach with diploma and a certified virtual team coach.</p>
  </section>
</main>
</body>
</html>
```